Vertical Banner

I need an eye-catching banner created for street fairs, indoor and outdoor events to draw attention to our language school. It will be to print on this banner (specs included):
https://www.banvoxprint.com/tag/617/Retractable-Banners/product/5174-46/Economy-Retractor-Banner-Display-27-09

I want the banner to be:
- SIMPLE
- Eye catching (not busy with too many pictures or information)
- It should say at top prominently: "Come learn a language!" and have our name.
- Below these languages should be large and eye-catching: Spanish, Chinese, French, Russian, German, Italian, Farsi, Turkish, Portuguese, ASL, Cantonese, Japanese, Korean, Vietnamese, Arabic, Dutch, more... (if some need to be cut our because of overcrowding let me know OR we can make some big and others small)
- Below this it should have GROUP & PRIVATE LESSONS
- It should be colorful and make people think of things international - perhaps national flags in background? Or images of world famous monuments? Could be image of adutls in a classroom. Sth that gets people excited about travel and language learning
- It should have our contact info VERY large at bottom:
Tovira Languages -
San Francisco, Silicon Valley & New York City
www.toviralanguagesf.com
415-629-5140
info@toviralanguagesf.com
(this can be smaller)
Four Wexmoor Plaza
Lobby 3
San Francisco, CA 94187

Hey Designers, please feel free to do a rough take on it. I don't need you to spend too much time, just give me a general idea of how you would make it look, then i know we can go from there later and refine it. Feel free to make it more of a quick sketch to show how you would do it.

Target Market(s)

adults from about 25-55 years old, educated, employed and typically world travellers

Industry/Entity Type

School

Colors
86cfc6
00a990
cadf82
acd036
9bcb3c
fbed22
f78f20
ffc214
f37122

Requirements
Must have
• Must be simple! Too many banners put way too much information and pictures. I want someone to walk by and immediately know we teach foreign languages. Must have bright colors and large font for languages offered
Should not have
• Should not be too full of images and design that distract the viewer from seeing the main thing I want them to see: that we teacher languages

```html
<!DOCTYPE html>
<html lang="en">
<head>
<meta charset="utf-8">
<title>Tovira Languages – Vertical Banner</title>
<link rel="stylesheet" href="https://fonts.googleapis.com/css2?family=Open+Sans:ital,wght@0,400;0,700;0,800;1,800&family=Roboto+Condensed:wght@300;400;700&display=swap">
<style>
  :root{
    --page:#e4e4e4;
    --white:#ffffff;
    --teal-light:#a3dbdc;
    --teal-haze:#d6efef;
    --teal-title:#2f7d84;
    --ink:#0c2f38;
    --navy:#053846;
    --skyline:#5d8d9a;
    --ring:#4f9a8c;
    --green:#4cb848;
    --red:#ec1c24;
    --l-pink:#e6176f;
    --l-orange:#f37122;
    --l-yellow:#f6a21a;
    --l-lime:#9bcb3c;
    --l-blue:#1e8fcf;
    --l-violet:#4a3f98;
    --l-olive:#6a9a3a;
  }
  *{margin:0;padding:0;box-sizing:border-box}
  html,body{width:1200px;height:1200px;overflow:hidden;background:var(--page)}
  .banner{
    position:absolute;left:382px;top:30px;width:435px;height:1140px;overflow:hidden;
    background:linear-gradient(to bottom,var(--white) 0,var(--white) 380px,var(--teal-light) 540px,var(--teal-light) 100%);
    font-family:"Open Sans",sans-serif;
  }
  .headline{position:absolute;left:0;top:40px;width:435px;text-align:center}
  .headline__come{display:block;font-weight:400;font-size:52px;line-height:56px;letter-spacing:24px;color:var(--teal-title);margin-left:-30px}
  .headline__learn{display:block;font-weight:800;font-size:54px;line-height:56px;color:var(--ink);margin-left:-30px}
  .headline__language{display:block;font-weight:800;font-size:58px;line-height:60px;margin-left:-16px;letter-spacing:-1px}
  .headline__language span:nth-child(1){color:var(--l-pink)}
  .headline__language span:nth-child(2){color:var(--l-orange)}
  .headline__language span:nth-child(3){color:var(--l-yellow)}
  .headline__language span:nth-child(4){color:var(--l-lime)}
  .headline__language span:nth-child(5){color:var(--l-blue)}
  .headline__language span:nth-child(6){color:var(--l-violet)}
  .headline__language span:nth-child(7){color:var(--l-orange)}
  .headline__language span:nth-child(8){color:var(--l-olive)}
  .headline__bang{position:absolute;left:372px;top:44px;font-weight:800;font-size:150px;line-height:150px;color:var(--red)}
  .brand-name{
    position:absolute;left:0;top:238px;width:435px;text-align:center;
    font-weight:800;font-size:66px;line-height:70px;color:var(--green);
  }
  .world{position:absolute;left:0;top:396px;width:435px;height:470px}
  .languages{position:absolute;left:0;top:0;width:435px;height:1140px;pointer-events:none}
  .lang-line{position:absolute;left:0;width:435px;display:flex;justify-content:center;align-items:baseline;gap:6px;color:var(--ink);white-space:nowrap;line-height:1}
  .xb{font-family:"Open Sans",sans-serif;font-weight:800}
  .rg{font-family:"Open Sans",sans-serif;font-weight:400}
  .cd{font-family:"Roboto Condensed",sans-serif;font-weight:400}
  .cdb{font-family:"Roboto Condensed",sans-serif;font-weight:700}
  .more{font-family:"Open Sans",sans-serif;font-weight:800;font-style:italic;color:var(--red)}
  .lessons{position:absolute;left:0;top:876px;width:435px;height:110px}
  .lessons__text{position:absolute;left:0;top:6px;width:435px;text-align:center;font-family:"Roboto Condensed",sans-serif;font-weight:700;font-size:28px;line-height:36px;color:var(--ink)}
  .lessons__icon{position:absolute;width:92px;height:92px;border-radius:50%;background:var(--white)}
  .lessons__icon--group{left:36px;top:-12px}
  .lessons__icon--private{left:310px;top:-8px}
  .footer{position:absolute;left:0;top:0;width:435px;height:1140px}
  .footer__text{position:absolute;left:0;top:978px;width:435px;text-align:center;color:var(--white);font-family:"Roboto Condensed",sans-serif;font-weight:700}
  .footer__name{font-size:36px;line-height:44px}
  .footer__region{font-size:20px;line-height:28px}
  .footer__contact{font-size:23px;line-height:34px;margin-top:6px}
  .footer__web{font-size:36px;line-height:40px}
</style>
</head>
<body>
<main class="banner">
  <h1 class="headline">
    <span class="headline__come">COME</span>
    <span class="headline__learn">LEARN A</span>
    <span class="headline__language"><span>L</span><span>A</span><span>N</span><span>G</span><span>U</span><span>A</span><span>G</span><span>E</span></span>
  </h1>
  <span class="headline__bang">!</span>

  <div class="brand-name">Tovira<br>Languages</div>

  <svg class="world" viewBox="0 0 435 470" role="img" aria-label="Illustration of world landmarks and city skylines ringing a globe, with hot-air balloons and planes">
    <defs>
      <radialGradient id="haze" cx="50%" cy="50%" r="50%">
        <stop offset="0" stop-color="#d6efef"/>
        <stop offset="1" stop-color="#a3dbdc" stop-opacity="0"/>
      </radialGradient>
    </defs>
    <rect width="435" height="470" fill="url(#haze)"/>
    <circle cx="211" cy="240" r="215" fill="var(--skyline)" opacity="0.85"/>
    <circle cx="211" cy="240" r="165" fill="var(--ring)"/>
    <circle cx="211" cy="240" r="161" fill="var(--white)"/>
  </svg>

  <div class="languages">
    <div class="lang-line" style="top:494px"><span class="xb" style="font-size:30px">SPANISH</span></div>
    <div class="lang-line" style="top:530px"><span class="rg" style="font-size:30px">CHINESE</span><span class="rg" style="font-size:22px">RUSSIAN</span></div>
    <div class="lang-line" style="top:562px"><span class="xb" style="font-size:34px;letter-spacing:-1px">FRENCH</span><span class="cd" style="font-size:38px">GERMAN</span></div>
    <div class="lang-line" style="top:598px"><span class="cd" style="font-size:42px;font-weight:300">ITALIAN</span><span class="xb" style="font-size:28px">FARSI</span></div>
    <div class="lang-line" style="top:637px"><span class="xb" style="font-size:28px">ASL</span><span class="xb" style="font-size:34px">TURKISH</span></div>
    <div class="lang-line" style="top:672px"><span class="rg" style="font-size:21px;letter-spacing:7px">PORTUGUESE</span></div>
    <div class="lang-line" style="top:693px"><span class="xb" style="font-size:26px">JAPANESE</span><span class="xb" style="font-size:20px">CANTONESE</span></div>
    <div class="lang-line" style="top:720px"><span class="xb" style="font-size:32px">KOREAN</span><span class="cd" style="font-size:30px">ARABIC</span></div>
    <div class="lang-line" style="top:752px"><span class="cd" style="font-size:22px">VIETNAMESE</span><span class="cdb" style="font-size:28px">DUTCH</span></div>
    <div class="lang-line" style="top:780px"><span class="more" style="font-size:20px">MORE.....</span></div>
  </div>

  <section class="lessons">
    <div class="lessons__icon lessons__icon--group" role="img" aria-label="Icon of a teacher presenting to a small group of students"></div>
    <div class="lessons__icon lessons__icon--private" role="img" aria-label="Icon of a tutor and one student at a desk"></div>
    <p class="lessons__text">GROUP &amp;<br>PRIVATE LESSONS</p>
  </section>

  <footer class="footer">
    <svg width="435" height="1140" viewBox="0 0 435 1140" style="position:absolute;left:0;top:0">
      <path d="M0 943 Q217 978 435 943 L435 1140 L0 1140 Z" fill="var(--navy)"/>
    </svg>
    <div class="footer__text">
      <div class="footer__name">Tovira Languages</div>
      <div class="footer__region">San Francisco, Silicon Valley &amp; New York City</div>
      <div class="footer__contact">415-629-5140 &nbsp;|&nbsp; info@toviralanguagesf.com</div>
      <div class="footer__web">www.toviralanguagesf.com</div>
    </div>
  </footer>
</main>
</body>
</html>
```